Business Card Design

We are looking for a business card designed for our landscaping company. We do landscaping installation & Maintenance Services. We would like to see designs that have basic landscaping in background. We also think it is important to have both of our names and phone numbers on the card. We need something that stands out a little whether it is shape of the card or thickness or design.

Business

Bramblewood Yardworks, bramblewoodyard@mailvista.net, Owen Platt 555-273-9104, Daniel Korbin 555-618-3927

```html
<!DOCTYPE html>
<html lang="en">
<head>
<meta charset="utf-8">
<title>Bramblewood Yardworks — Business Card</title>
<link href="https://fonts.googleapis.com/css2?family=Bodoni+Moda:wght@500&family=Open+Sans:wght@400&display=swap" rel="stylesheet">
<style>
  :root {
    --backdrop: #e7e5e1;
    --card-white: #fbfbfb;
    --card-shade: #ececec;
    --leaf-green: #12c06a;
    --ink-black: #0b0b0b;
    --text-dark: #161616;
    --text-mid: #333333;
  }
  html, body {
    margin: 0;
    padding: 0;
    width: 1200px;
    height: 892px;
    overflow: hidden;
    background: var(--backdrop);
  }
  .business-card {
    position: absolute;
    left: 150px;
    top: 189px;
    width: 900px;
    height: 514px;
    border-radius: 30px;
    overflow: hidden;
    background: linear-gradient(160deg, var(--card-white) 0%, #f4f4f4 60%, var(--card-shade) 100%);
    box-shadow: 0 14px 34px rgba(0,0,0,0.18);
  }
  .card-accents {
    position: absolute;
    inset: 0;
    width: 900px;
    height: 514px;
  }
  .company-name {
    position: absolute;
    left: 0;
    right: 0;
    top: 92px;
    margin: 0;
    text-align: center;
    font-family: "Bodoni Moda", "Didot", serif;
    font-weight: 500;
    font-size: 52px;
    letter-spacing: 0.5px;
    color: var(--text-dark);
  }
  .company-email {
    position: absolute;
    left: 0;
    right: 0;
    top: 172px;
    margin: 0;
    text-align: center;
    font-family: "Open Sans", Arial, sans-serif;
    font-size: 22px;
    color: var(--text-mid);
  }
  .contact {
    position: absolute;
    top: 262px;
  }
  .contact--owen { left: 300px; }
  .contact--daniel { left: 590px; }
  .contact-name {
    margin: 0;
    font-family: "Bodoni Moda", "Didot", serif;
    font-weight: 500;
    font-size: 32px;
    color: var(--text-dark);
  }
  .contact-phone {
    margin: 6px 0 0 0;
    display: flex;
    align-items: center;
    gap: 10px;
    font-family: "Open Sans", Arial, sans-serif;
    font-size: 24px;
    color: var(--text-dark);
  }
  .phone-icon {
    width: 18px;
    height: 18px;
  }
</style>
</head>
<body>
  <div class="business-card">
    <svg class="card-accents" viewBox="0 0 900 514" aria-hidden="true">
      <path d="M0 300 Q 200 470 900 514 L 0 514 Z" fill="var(--ink-black)"/>
      <path d="M0 296 L 70 296 Q 120 420 190 470 Q 60 410 0 330 Z" fill="var(--leaf-green)"/>
      <path d="M330 490 Q 600 508 900 514 L 900 470 Z" fill="var(--leaf-green)"/>
      <path d="M0 300 Q 200 470 900 514 L 900 500 Q 230 450 0 282 Z" fill="#ffffff"/>
    </svg>

    <h1 class="company-name">Bramblewood Yardworks</h1>
    <p class="company-email">bramblewoodyard@mailvista.net</p>

    <div class="contact contact--owen">
      <p class="contact-name">Owen Platt</p>
      <p class="contact-phone">
        <svg class="phone-icon" viewBox="0 0 18 18" aria-hidden="true">
          <rect width="18" height="18" rx="2" fill="var(--ink-black)"/>
          <path d="M5 4 L7.5 4 L8.3 6.8 L7 7.8 Q8 10.2 10.2 11.2 L11.2 9.9 L14 10.7 L14 13.2 Q8 14 4.6 8 Q4.2 6 5 4 Z" fill="#ffffff"/>
        </svg>
        555-273-9104
      </p>
    </div>

    <div class="contact contact--daniel">
      <p class="contact-name">Daniel Korbin</p>
      <p class="contact-phone">
        <svg class="phone-icon" viewBox="0 0 18 18" aria-hidden="true">
          <rect width="18" height="18" rx="2" fill="var(--ink-black)"/>
          <path d="M5 4 L7.5 4 L8.3 6.8 L7 7.8 Q8 10.2 10.2 11.2 L11.2 9.9 L14 10.7 L14 13.2 Q8 14 4.6 8 Q4.2 6 5 4 Z" fill="#ffffff"/>
        </svg>
        555-618-3927
      </p>
    </div>
  </div>
</body>
</html>
```